Home Page Design (PSD Only) - Ecommerce - Yarn, Apparel and Socks

We need a new home page design for our e-commerce site WoolHarbor.com.
Our team will create the HTML/CSS using the Scaffoldy framework. We just need the final PSD and slices. Our brand/logo will remain however our focus has shifted to two key product categories. 1: Yarn 2: Socks. We also sell products in the other categories but these will not be the focus and jewelry will likely go away.

Our socks and yarn are focused on "Affordable Luxury" We carry over 2000 yarns (Huge Selection) and have the largest selection on the internet for Alpaca Socks.

Our buyers are very different. Most yarn buyers are women 25-55 who are very tactile. They want to feel the yarn so this somehow needs to come through. Clean and Warm, Affordable Luxury.

Our sock buyers buy premium socks ($15-20/pair) are split male/female and have little interest in Yarn or Knitting. I realize we should likely have 2 different sites but we've spent 7 years building the brand and have loyalty from both markets and are not getting x-sell. Especially knitters who buy our socks and stuffed bears, etc for gifts.

We'll be moving toward a new responsive design based on the Scaffoldy framework under the hood.
Updates

Project Deadline Extended
Reason: Requested by some designers to make additional changes.

Project Deadline Extended
Reason: We received more feedback from customers so need to get this feedback to designers.

Target Market(s)

Women for the Yarn (knitters). Split 60F/40M for socks
Current site is blue. Feel free to update the colors to make the site more attractive for women.

Industry/Entity Type

E-Commerce

Requirements
Must have
• Rotating Hero, Global Search, Must incorporate our blue logo (or inverse). Social bar for Chirpline, Friendwall, Clipboardia, Loopmeet (yarn social site), Stitchspark (yarn social site).
Can use warm colors to appeal more to women.
Must support a responsive design (scaffoldy)
Nice to have
• Site should resonate with Knitters but not alienate users who just come to shop for Socks, Stuffed Bears, Sweaters, etc.
Clean, simple design, but with warmth and upscale feeling.
Yarn sites: fibrebarn.example, loomcrate.example
Sock/Apparel Sites: toastytoes.example, stridewell.example, cedarvale.example, tuv.example

I've added some initial comps that tested OK but early feedback was it was too plain and lacked emotional appeal.

```html
<!DOCTYPE html>
<html lang="en">
<head>
<meta charset="utf-8">
<title>WoolHarbor – Home</title>
<link rel="stylesheet" href="https://fonts.googleapis.com/css2?family=Roboto:wght@300;400&family=Mulish:wght@400;600&display=swap">
<style>
:root{
  --bg:#5f5852;
  --panel:#f8e4cc;
  --white:#ffffff;
  --nav:#383838;
  --ink:#444444;
  --muted:#6a6a6a;
  --brand:#1a6fc0;
  --caption:rgba(40,40,40,.88);
  --line:#e6e6e6;
  --soft-text:#f3efea;
}
*{box-sizing:border-box;margin:0;padding:0}
html,body{width:1013px;height:1200px;overflow:hidden}
body{background:var(--bg);font-family:"Roboto",Arial,sans-serif;position:relative;color:var(--ink)}
.abs{position:absolute}

/* header */
.brand{left:104px;top:34px;display:flex;align-items:center;gap:10px;color:var(--brand);font-family:"Mulish",sans-serif;font-weight:600;font-size:34px;letter-spacing:-.3px;line-height:40px}
.brand-dot{width:20px;height:20px;border-radius:50%;background:var(--brand)}
.top-links{top:40px;text-align:right;font-size:10px;line-height:15.5px;color:var(--soft-text);font-weight:300;letter-spacing:.2px}
.top-links.col-a{right:291px}
.top-links.col-b{right:154px}
.bag{left:879px;top:34px;width:34px;height:48px}

/* nav */
.nav{left:93px;top:105px;width:839px;height:34px}
.nav-items{top:105px;height:34px;color:#fff;font-size:11px;line-height:34px}
.home-icon{left:116px;top:114px;width:16px;height:15px}
.search{left:735px;top:112px;width:149px;height:20px;background:#fff;font-size:10px;color:#555;padding:4px 5px;line-height:12px}
.search-icon{left:894px;top:114px;width:15px;height:15px}

/* content panel */
.panel{left:101px;top:139px;width:810px;height:754px;background:var(--panel)}
.page-title{left:101px;top:147px;width:810px;text-align:center;font-family:"Mulish",sans-serif;font-size:22px;font-weight:400;color:var(--ink)}

.hero{left:118px;top:184px;width:777px;height:307px;background:var(--white)}
.hero-art{left:118px;top:196px;width:400px;height:285px;background:linear-gradient(100deg,#ffffff 0%,#f4e7d6 18%,#eccfd8 38%,#f3e6b4 58%,#e6ecef 78%,#ffffff 100%)}
.hero-title{left:571px;top:268px;width:246px;height:41px;background:var(--nav);color:#fff;font-family:"Mulish",sans-serif;font-size:26px;padding:4px 7px;line-height:31px;white-space:nowrap}
.hero-copy{left:571px;top:309px;width:246px;height:94px;background:var(--nav);color:#eee;font-family:"Mulish",sans-serif;font-size:10.3px;line-height:15.3px;padding:8px 7px}
.arrow{top:308px;width:26px;height:53px}
.arrow.prev{left:101px}
.arrow.next{left:886px}

/* tabs */
.tab{top:516px;height:28px;background:#fdf3e6;font-size:10.3px;color:#333;text-align:center;line-height:27px}
.tab.active{background:#fff;color:var(--brand)}
.products{left:118px;top:543px;width:777px;height:159px;background:var(--white)}
.divider{top:543px;width:1px;height:159px;background:var(--line)}
.thumb{top:557px;height:110px;border-radius:6px}
.p-name{top:672px;font-size:10px;color:var(--muted);line-height:15px;letter-spacing:.2px}

/* promos */
.promo{top:722px;width:253px;height:152px;background:#fff;padding:4px}
.promo-img{width:100%;height:100%;position:relative}
.promo-cap{position:absolute;left:0;right:0;bottom:0;height:32px;background:var(--caption);color:#fff;font-family:"Mulish",sans-serif;font-size:15px;line-height:32px;padding-left:9px}

/* footer */
.footer{left:101px;top:893px;width:810px;height:179px;background:var(--white)}
.f-col{top:932px}
.f-col h4{font-family:"Mulish",sans-serif;font-weight:600;font-size:12.5px;color:#444;margin-bottom:12px}
.f-col li{list-style:none;font-size:10.3px;color:#555;line-height:19.4px}

/* bottom */
.card{top:1100px;width:35px;height:23px;border-radius:3px}
.badge{left:316px;top:1095px;width:66px;height:33px;border-radius:17px;background:#f3eee4}
.follow{left:676px;top:1093px;font-family:"Mulish",sans-serif;font-size:18px;color:#fff}
.social{top:1091px;width:28px;height:28px;border-radius:3px}
.legal{left:102px;top:1141px;width:560px;font-size:10.2px;line-height:15.2px;color:var(--soft-text)}
.copy{left:739px;top:1141px;font-size:10.2px;line-height:15.2px;color:var(--soft-text)}
</style>
</head>
<body>

<header>
  <div class="abs brand"><span class="brand-dot"></span>WoolHarbor</div>
  <div class="abs top-links col-a">Join Our Newsletter<br>Our Stores<br>A- Z Brands</div>
  <div class="abs top-links col-b">Shopping Bag: &nbsp;£0.00<br>My Account<br>My Wish List</div>
  <svg class="abs bag" viewBox="0 0 34 48" aria-label="Shopping bag, 0 items">
    <path d="M10 12 Q17 -2 24 12" fill="none" stroke="#d9c49a" stroke-width="1.5"/>
    <path d="M3 12 H31 L33 46 H1 Z" fill="#e9d3a6"/>
    <text x="17" y="34" font-family="Roboto, sans-serif" font-size="17" fill="#8c6d3d" text-anchor="middle">0</text>
  </svg>
</header>

<nav>
  <svg class="abs nav" viewBox="0 0 839 34" preserveAspectRatio="none"><path d="M7 0 H839 L832 34 H0 Z" fill="#383838"/></svg>
  <svg class="abs home-icon" viewBox="0 0 16 15"><path d="M8 1 L15 8 H13 V14 H10 V10 H6 V14 H3 V8 H1 Z" fill="#fff"/></svg>
  <span class="abs nav-items" style="left:149px">Women</span>
  <span class="abs nav-items" style="left:213px">Men</span>
  <span class="abs nav-items" style="left:260px">Kids</span>
  <span class="abs nav-items" style="left:306px">Home Goods</span>
  <span class="abs nav-items" style="left:398px">Jewelry</span>
  <span class="abs nav-items" style="left:463px">Yarn &amp; Fiber</span>
  <span class="abs nav-items" style="left:549px">Gifts</span>
  <span class="abs nav-items" style="left:596px">Clearance</span>
  <div class="abs search">Search Products...</div>
  <svg class="abs search-icon" viewBox="0 0 15 15"><circle cx="6" cy="6" r="4.3" fill="none" stroke="#fff" stroke-width="2"/><path d="M9 9 L14 14" stroke="#fff" stroke-width="2.4"/></svg>
</nav>

<main>
  <div class="abs panel"></div>
  <h1 class="abs page-title">Alpaca &amp; Pima Cotton Apparel Direct Merchants</h1>

  <section>
    <div class="abs hero"></div>
    <div class="abs hero-art" role="img" aria-label="Photo of balls of coloured yarn with knitting needles"></div>
    <div class="abs hero-title">WoolHarbor Yarn</div>
    <p class="abs hero-copy">Sed ut perspiciatis unde omnis iste natus error sit voluptatem accusantium doloremque laud-antium, totam rem aperiam, eaque ipsa quae ab illo inventore veritatis et quasi architecto beatae vitae dicta sunt explicabo.</p>
    <svg class="abs arrow prev" viewBox="0 0 26 53"><path d="M0 0 A26 26.5 0 0 1 0 53 Z" fill="#fff" stroke="#ddd"/><path d="M15 19 L9 26.5 L15 34" fill="none" stroke="#444" stroke-width="2"/></svg>
    <svg class="abs arrow next" viewBox="0 0 26 53"><path d="M26 0 A26 26.5 0 0 0 26 53 Z" fill="#fff" stroke="#ddd"/><path d="M11 19 L17 26.5 L11 34" fill="none" stroke="#444" stroke-width="2"/></svg>
  </section>

  <section>
    <div class="abs tab active" style="left:117px;width:80px">Just Arrived</div>
    <div class="abs tab" style="left:199px;width:81px">Best Sellers</div>
    <div class="abs tab" style="left:284px;width:68px">Womens</div>
    <div class="abs tab" style="left:355px;width:52px">Mens</div>
    <div class="abs tab" style="left:410px;width:52px">Kids</div>

    <div class="abs products"></div>
    <div class="abs divider" style="left:252px"></div>
    <div class="abs divider" style="left:391px"></div>
    <div class="abs divider" style="left:548px"></div>
    <div class="abs divider" style="left:679px"></div>

    <div class="abs thumb" style="left:138px;width:92px;background:linear-gradient(#f4ecea,#d9c0c0)" role="img" aria-label="Photo of patterned alpaca yarn socks"></div>
    <div class="abs thumb" style="left:279px;width:85px;background:linear-gradient(#f1ece4,#ddd3c4)" role="img" aria-label="Photo of a cream cable-knit sweater"></div>
    <div class="abs thumb" style="left:420px;width:102px;background:linear-gradient(#f1e7dc,#d9c1a6)" role="img" aria-label="Photo of a tan ribbed knit cap"></div>
    <div class="abs thumb" style="left:580px;width:72px;background:linear-gradient(#f3e9f0,#e2d3e6)" role="img" aria-label="Photo of a striped multicolour muffler"></div>
    <div class="abs thumb" style="left:706px;width:160px;background:linear-gradient(#eaf1f7,#c9dcec)" role="img" aria-label="Photo of blue knit running shoes"></div>

    <p class="abs p-name" style="left:135px">Alpaca Yarn Socks<br>£120.00</p>
    <p class="abs p-name" style="left:269px">Alpaca Yarn Sweaters<br>£120.00</p>
    <p class="abs p-name" style="left:418px">Alpaca Yarn Cap<br>£120.00</p>
    <p class="abs p-name" style="left:571px">Alpaca Yarn Muffler<br>£120.00</p>
    <p class="abs p-name" style="left:708px">Alpaca Yarn Shoes<br>£120.00</p>
  </section>

  <section>
    <div class="abs promo" style="left:118px"><div class="promo-img" role="img" aria-label="Photo of a woman in a patterned knit sweater outdoors" style="background:linear-gradient(#a07a62,#7d5a48)"><div class="promo-cap">Alpaca 2000 Yarns</div></div></div>
    <div class="abs promo" style="left:381px"><div class="promo-img" role="img" aria-label="Photo of a woman in a winter hat and knit scarf" style="background:linear-gradient(#eef0f2,#aeb9c4)"><div class="promo-cap">Alpaca 2000 Yarns</div></div></div>
    <div class="abs promo" style="left:642px"><div class="promo-img" role="img" aria-label="Photo of a woman in a yellow knit cardigan" style="background:linear-gradient(#ecebe2,#e6cf5a)"><div class="promo-cap">Alpaca 2000 Yarns</div></div></div>
  </section>
</main>

<footer>
  <div class="abs footer"></div>
  <div class="abs f-col" style="left:145px"><h4>About Alpaca</h4><ul><li>Our Story</li><li>Our Stores</li><li>A- Z of Brands</li><li>We Love</li></ul></div>
  <div class="abs f-col" style="left:297px"><h4>Customer Services</h4><ul><li>FAQs</li><li>Deliver Info</li><li>Returns &amp; Exchanges</li><li>Contact Us</li></ul></div>
  <div class="abs f-col" style="left:483px"><h4>More ...</h4><ul><li>Shoe Finder</li><li>My Wish List</li><li>Size Guide</li><li>Recruitment</li><li>Security</li></ul></div>
  <div class="abs f-col" style="left:618px"><h4>Why Alpaca</h4><ul><li>lorem ipsum</li><li>dolor sit</li><li>amet consectetur</li><li>adipisicing elit</li></ul></div>
  <div class="abs f-col" style="left:771px"><h4>Contact Us</h4><ul><li>lorem ipsum</li><li>dolor sit</li><li>amet consectetur</li><li>adipisicing elit</li></ul></div>

  <div class="abs card" style="left:103px;background:#f4f4f4" aria-label="Payment card"></div>
  <div class="abs card" style="left:142px;background:#1d4f91" aria-label="Payment card"></div>
  <div class="abs card" style="left:181px;background:#d8412f" aria-label="Payment card"></div>
  <div class="abs card" style="left:221px;background:#2a5aa8" aria-label="Payment card"></div>
  <div class="abs card" style="left:260px;background:#f2e6b4" aria-label="Payment method"></div>
  <div class="abs badge" aria-label="Security badge"></div>

  <div class="abs follow">follow us...</div>
  <div class="abs social" style="left:782px;background:#3b5c9a" aria-label="Friendwall"></div>
  <div class="abs social" style="left:815px;background:#3aa6e0" aria-label="Chirpline"></div>
  <div class="abs social" style="left:848px;background:#c8232c" aria-label="Clipboardia"></div>
  <div class="abs social" style="left:882px;background:#e8e4de" aria-label="Photo sharing"></div>

  <p class="abs legal">Lorem ipsum dolor sit amet, consectetur adipisicing elit, sed do eiusmod tempor incididunt ut labore et dolore magna aliqua. Ut enim ad minim veniam, quis nostrud exercitation ullamco laboris nisi ut aliquip ex ea commodo consequat.<br>More Detail</p>
  <p class="abs copy">© 2013 WoolHarbor. All Rights Reserved.<br>Terms &amp; Condition &nbsp;&nbsp;| &nbsp;&nbsp;Privacy Policy</p>
</footer>

</body>
</html>
```